Halverstone Minerals Web Design

Require a Web page design for an international mining and private investment company currently based in Dubai, UAE. I would like to view designs that incorporate our current corporate logo design aimed at communicating global business development/expansion across a diversity of commodities within the mining and investment sectors.

We are a global organisation with global experience and strategy with specific business development focus in Africa, Central and South America.

Target Market(s)

Mining industry, finance, fund raising, brokering, private equity and public stock exchanges.

Industry/Entity Type

Mining

Number of Pages Required

5+ page

Font styles to use
Sans Serif

Colors

Designer to choose colors to be used in the design.

Requirements
Must have
• Corporate logo, description of who we are, what we do, corporate mission, vision & strategy.
Nice to have
• Inclusion of images, photos, interactive maps/graphics and video.

```html
<!DOCTYPE html>
<html lang="en">
<head>
<meta charset="utf-8">
<title>Halverstone Minerals</title>
<link href="https://fonts.googleapis.com/css2?family=Lato:wght@400;700&family=Open+Sans:wght@400;600&display=swap" rel="stylesheet">
<style>
:root{
  --gold:#c8a65a;
  --gold-dark:#b08d45;
  --gold-light:#dcc183;
  --ink:#2b2b2b;
  --text:#5c5c5c;
  --white:#ffffff;
  --grey:#d9d9d9;
  --footer:#1b1b1b;
  --footer-text:#bdbdbd;
}
*{margin:0;padding:0;box-sizing:border-box}
html,body{width:1200px;height:3158px;overflow:hidden}
body{position:relative;background:var(--white);font-family:"Open Sans",Arial,sans-serif;color:var(--text)}
.abs{position:absolute}
.heading{font-family:"Lato",Arial,sans-serif;text-transform:uppercase;letter-spacing:.5px}
.btn{position:absolute;display:flex;align-items:center;justify-content:center;background:var(--gold);color:var(--white);font-family:"Lato",Arial,sans-serif;font-weight:700;font-size:14px;text-transform:uppercase;letter-spacing:.5px}
p.body{font-size:14px;line-height:26px;color:var(--text)}

/* hero */
.hero{position:absolute;left:0;top:0;width:1200px;height:712px;overflow:hidden}
.hero-photo{position:absolute;inset:0;background:radial-gradient(ellipse at 55% 45%,#6f6a5c 0%,#4a4a46 35%,#2c3038 70%,#1f2430 100%)}
.hero-shade{position:absolute;inset:0;background:linear-gradient(180deg,rgba(10,14,25,.55) 0%,rgba(10,14,25,.15) 40%,rgba(0,0,0,0) 100%)}
.brand{position:absolute;left:95px;top:32px;display:flex;align-items:center;gap:10px;color:var(--gold);font-family:"Lato",Arial,sans-serif;font-weight:700;font-size:18px;white-space:nowrap;text-transform:uppercase;letter-spacing:.5px}
.brand-mark{width:26px;height:26px;background:var(--gold)}
.nav{position:absolute;left:420px;top:41px;display:flex;gap:16px;white-space:nowrap;font-family:"Lato",Arial,sans-serif;font-weight:700;font-size:13px;text-transform:uppercase;color:var(--white)}
.nav .active{color:var(--gold)}
.hero-title{position:absolute;left:0;top:250px;width:1200px;text-align:center;color:var(--white);font-family:"Lato",Arial,sans-serif;font-weight:700;font-size:38px;line-height:50px;text-transform:uppercase}
.hero-btn{left:516px;top:368px;width:172px;height:40px;text-transform:none;font-size:16px;font-weight:400;font-family:"Open Sans",Arial,sans-serif}
.slider{position:absolute;left:553px;top:628px;display:flex;align-items:center;gap:6px}
.slider .arrow{width:20px;height:20px;border-radius:50%;background:var(--white);display:flex;align-items:center;justify-content:center}
.slider .dot{width:8px;height:8px;border-radius:50%;background:rgba(255,255,255,.6)}
.slider .dot.on{background:var(--white)}

/* what we do */
.wwd-frame{left:114px;top:819px;width:490px;height:335px;border:2px solid var(--gold)}
.wwd-title{left:170px;top:862px;font-size:28px;color:var(--gold);font-weight:400}
.wwd-text{left:170px;top:908px;width:400px}
.wwd-photo{left:602px;top:773px;width:490px;height:416px;background:linear-gradient(135deg,#f4e3a6 0%,#c7a76a 45%,#7f9a3e 70%,#a6825a 100%);box-shadow:0 12px 30px rgba(0,0,0,.3)}

/* projects */
.projects{left:0;top:1326px;width:1200px;height:526px;background:linear-gradient(180deg,#c9a85d 0%,#b99548 100%)}
.projects-title{left:0;top:1378px;width:1200px;text-align:center;color:var(--white);font-size:28px;font-weight:400}
.project{position:absolute;top:1444px;width:324px;height:284px}
.project .label{position:absolute;left:12px;right:12px;top:229px;height:40px;background:rgba(255,255,255,.88);display:flex;align-items:center;justify-content:center;font-family:"Lato",Arial,sans-serif;font-size:18px;color:var(--ink);text-transform:uppercase}

/* mission / vision */
.pillar{position:absolute;top:1941px;height:300px;color:var(--white);text-align:center}
.pillar .icon{position:absolute;left:50%;top:34px;transform:translateX(-50%)}
.pillar .title{position:absolute;left:0;right:0;top:98px;font-size:23px;font-weight:700}
.pillar .copy{position:absolute;left:60px;right:60px;top:138px;font-size:13px;line-height:21px;color:rgba(255,255,255,.85)}
.pillar .btn{left:50%;transform:translateX(-50%);top:214px;width:144px;height:40px}

/* who we are */
.who{left:0;top:2326px;width:1200px;height:448px;background:var(--grey)}
.who-photo{left:0;top:2326px;width:820px;height:448px;background:linear-gradient(90deg,#8a6a52 0%,#9c8372 40%,#b6aaa0 70%,rgba(217,217,217,0) 100%)}
.who-title{left:688px;top:2420px;font-size:28px;color:var(--ink);font-weight:400}
.who-text{left:688px;top:2466px;width:400px}

/* footer */
.footer{left:0;top:2774px;width:1200px;height:384px;background:var(--footer)}
.f-col{position:absolute;top:2840px}
.f-col h4{font-family:"Lato",Arial,sans-serif;font-weight:400;text-transform:uppercase;font-size:19px;color:var(--white);margin-bottom:16px}
.f-col li{list-style:none;font-size:14px;line-height:31px;color:var(--footer-text)}
.f-contact li{display:flex;gap:14px;align-items:flex-start;line-height:26px;margin-bottom:4px}
.f-contact svg{flex:none;margin-top:5px}
.f-div{position:absolute;top:2846px;width:1px;height:174px;background:#4a4a4a}
.socials{display:flex;gap:22px;margin-top:6px}
.socials span{width:18px;height:18px;border-radius:50%;background:var(--gold)}
.f-rule{left:128px;top:3088px;width:944px;height:1px;background:#3a3a3a}
.copyright{left:0;top:3112px;width:1200px;text-align:center;font-size:12px;color:#8a8a8a}
</style>
</head>
<body>

<header class="hero">
  <div class="hero-photo" role="img" aria-label="Aerial view of a terraced open-pit mine"></div>
  <div class="hero-shade"></div>
  <svg class="abs" style="left:0;top:0" width="1200" height="712" viewBox="0 0 1200 712" aria-hidden="true">
    <polygon points="0,530 180,560 330,520 540,545 760,515 980,470 1200,420 1200,712 0,712" fill="#c4a25a"/>
    <polygon points="0,530 180,560 320,712 0,712" fill="#b8964c"/>
    <polygon points="540,545 760,515 900,600 700,712 520,712" fill="#cfae66"/>
    <polygon points="980,470 1200,420 1200,712 1060,712" fill="#d3b46e"/>
    <polygon points="330,520 540,545 420,650" fill="#bc9a52"/>
  </svg>
  <div class="brand"><span class="brand-mark"></span>Halverstone Minerals</div>
  <nav class="nav">
    <span class="active">Home</span><span>Who we are</span><span>What we do</span><span>Corporate mission</span><span>Vision &amp; strategy</span><span>Contact us</span>
  </nav>
  <h1 class="hero-title">International mining, project<br>development &amp; investment experience</h1>
  <div class="btn hero-btn">Learn More ›</div>
  <div class="slider">
    <span class="arrow"><svg width="8" height="10"><polygon points="6,0 0,5 6,10" fill="#333"/></svg></span>
    <span class="dot on"></span><span class="dot"></span><span class="dot"></span><span class="dot"></span>
    <span class="arrow"><svg width="8" height="10"><polygon points="2,0 8,5 2,10" fill="#333"/></svg></span>
  </div>
</header>

<section>
  <div class="abs wwd-frame"></div>
  <h2 class="abs heading wwd-title">What we do</h2>
  <div class="abs wwd-text">
    <p class="body">Praesent elementum elit at tellus nec ultricies sit amet porttitor mattis enim In massa libero</p>
    <p class="body" style="margin-top:10px">interdum nec interdum vel blandit sed nulla In ullamcorper est eget tempor cursus neque mi consecte tuer mi a ultricies massa est sed nisl Class</p>
  </div>
  <div class="btn" style="left:170px;top:1067px;width:144px;height:40px">Read more</div>
  <div class="abs wwd-photo" role="img" aria-label="Seedlings growing from stacks of coins"></div>
</section>

<section>
  <div class="abs projects"></div>
  <h2 class="abs heading projects-title">Our projects</h2>
  <div class="project" style="left:95px;background:linear-gradient(180deg,#8fb3d6 0%,#5f8a3e 30%,#c0643a 60%,#b0553a 100%)" role="img" aria-label="Cleared red-earth mining site at forest edge">
    <div class="label">Project title here</div></div>
  <div class="project" style="left:438px;background:linear-gradient(180deg,#3d5e2a 0%,#6e9a3c 45%,#2f4d1f 100%)" role="img" aria-label="Dense green forest with sunlight">
    <div class="label">Project title here</div></div>
  <div class="project" style="left:781px;background:linear-gradient(180deg,#9aa0a6 0%,#55595e 50%,#3a3d40 100%)" role="img" aria-label="Haul trucks in a grey coal mine">
    <div class="label">Project title here</div></div>
  <svg class="abs" style="left:0;top:1764px" width="1200" height="90" viewBox="0 0 1200 90" aria-hidden="true">
    <polygon points="0,90 0,72 130,56 300,50 420,30 520,24 612,0 700,30 880,42 1000,52 1100,60 1200,62 1200,90" fill="#ffffff"/>
  </svg>
</section>

<section>
  <div class="pillar" style="left:107px;width:480px;background:linear-gradient(180deg,#4c6a44 0%,#7d5b45 55%,#5c6a5a 100%)" role="img" aria-label="Forest clearing with red soil and water">
    <svg class="icon" width="44" height="48" viewBox="0 0 44 48" fill="none" stroke="#fff" stroke-width="2"><path d="M30 4c6 0 10 4 10 10L22 32l-6-6L30 4z"/><path d="M16 26l-8 2 6-10h8M22 32l-2 8 10-6v-8"/><path d="M12 36l-6 6"/></svg>
    <div class="title heading">Corporate mission</div>
    <div class="copy">Praesent elementum elit at tellus nec ultricies sit amet porttitor mattis enim In massa libero interdum nec interdum vel blandit</div>
    <div class="btn">Read more</div>
  </div>
  <div class="pillar" style="left:617px;width:482px;background:linear-gradient(180deg,#6d7480 0%,#4e6a3e 45%,#8a6e52 100%)" role="img" aria-label="Mining site surrounded by forest under cloudy sky">
    <svg class="icon" width="40" height="48" viewBox="0 0 40 48" fill="none" stroke="#fff" stroke-width="2"><path d="M20 10a11 11 0 0 0-7 19c2 2 3 4 3 6h8c0-2 1-4 3-6a11 11 0 0 0-7-19z"/><path d="M16 40h8M17 44h6M20 2v3M6 8l2 2M34 8l-2 2M2 20h3M35 20h3"/></svg>
    <div class="title heading">Vision &amp; strategy</div>
    <div class="copy">Praesent elementum elit at tellus nec ultricies sit amet porttitor mattis enim In massa libero interdum nec interdum vel blandit</div>
    <div class="btn">Read more</div>
  </div>
</section>

<section>
  <div class="abs who"></div>
  <div class="abs who-photo" role="img" aria-label="Terraced walls of an open-pit mine"></div>
  <h2 class="abs heading who-title">Who we are</h2>
  <div class="abs who-text">
    <p class="body">Praesent elementum elit at tellus nec ultricies sit amet porttitor mattis enim In massa libero</p>
    <p class="body" style="margin-top:10px">interdum nec interdum vel blandit sed nulla In ullamcorper est eget tempor cursus neque mi consecte tuer mi a ultricies massa est sed nisl Class</p>
  </div>
  <div class="btn" style="left:688px;top:2627px;width:144px;height:40px">Read more</div>
</section>

<footer>
  <div class="abs footer"></div>
  <div class="f-col" style="left:116px"><h4>Company</h4><ul><li>Home</li><li>Who we are</li><li>What we do</li><li>Corporate mission</li></ul></div>
  <div class="f-div" style="left:272px"></div>
  <div class="f-col" style="left:320px"><h4>Resources</h4><ul><li>Vision &amp; strategy</li><li>News</li><li>Sitemap</li><li>Contact us</li></ul></div>
  <div class="f-div" style="left:486px"></div>
  <div class="f-col f-contact" style="left:539px"><h4>Contact us</h4><ul>
    <li><svg width="14" height="18" viewBox="0 0 14 18"><path d="M7 0a7 7 0 0 0-7 7c0 5 7 11 7 11s7-6 7-11a7 7 0 0 0-7-7zm0 10a3 3 0 1 1 0-6 3 3 0 0 1 0 6z" fill="#fff"/></svg><span>48 Harbor Ridge Road #4B<br>Austin 78701 TX</span></li>
    <li><svg width="16" height="16" viewBox="0 0 16 16"><path d="M3 0l3 4-2 2c1 2 4 5 6 6l2-2 4 3-2 3C7 16 0 9 0 3z" fill="#fff"/></svg><span>555.014.2270</span></li>
    <li><svg width="16" height="12" viewBox="0 0 16 12"><rect width="16" height="12" fill="#fff"/><path d="M0 0l8 6 8-6" fill="none" stroke="#1b1b1b" stroke-width="1.5"/></svg><span>info@halverstone-minerals.com</span></li>
  </ul></div>
  <div class="f-div" style="left:832px"></div>
  <div class="f-col" style="left:901px"><h4>Follow us</h4>
    <div class="socials"><span aria-label="Social profile"></span><span aria-label="Social profile"></span><span aria-label="Social profile"></span><span aria-label="Social profile"></span></div>
  </div>
  <div class="abs f-rule"></div>
  <div class="abs copyright">© 2018 Halverstone Minerals. All right reserved</div>
</footer>

</body>
</html>
```